Create a Professional PowerPoint Slide Deck

I need a professional looking and editable PowerPoint presentation with contents based on the attached PDF.

I would like to see the following;
- add design elements to every slide (cover, title, contents etc)
- enhance the graphs or charts
- same copy will be used
I'm attaching the document to be put into powerpoint (KVRD white paper: "Haul Wise")

Target Market(s)

Executives and managers responsible for the distribution of products

Industry/Entity Type

It Professional

Font styles to use
Serif

Colors

Designer to choose colors to be used in the design.

Requirements
Must have
• The format should be portrait orientation as this may be printed on paper and converted to PDF for distribution
• Complete conversion of all pages in the attached White Paper
• Upgraded graphics and formatting
Nice to have
• Any creative ideas to make the presentation more attractive or easier to understand
• Color scheme should complement the KVRD Freightworks Logo (red and black)

```html
<!DOCTYPE html>
<html lang="en">
<head>
<meta charset="utf-8">
<title>KVRD Freightworks – Use Your Data to Improve Logistics</title>
<link href="https://fonts.googleapis.com/css2?family=Source+Serif+4:opsz,wght@8..60,400;8..60,700&display=swap" rel="stylesheet">
<style>
  :root{
    --backdrop:#e4e4e4;
    --paper:#ffffff;
    --red:#e3151f;
    --ink:#2a2a2a;
    --body:#555555;
    --muted:#9a9a9a;
    --rule:#d6d6d6;
    --panel:#f0f0f0;
    --circle:#b9b9b9;
    --sheet-line:#e2e2e2;
  }
  *{box-sizing:border-box;margin:0;padding:0}
  html,body{width:1200px;height:800px;overflow:hidden;background:var(--backdrop);font-family:"Source Serif 4",Georgia,serif}
  .page{position:absolute;background:var(--paper);width:504px;height:671px;top:64px}
  .page--left{left:57px}
  .page--right{left:636px;height:674px}
  .abs{position:absolute}
  .running-head{left:36px;top:32px;font-size:11.5px;font-weight:700;line-height:13px}
  .running-head .kicker{color:var(--red)}
  .running-head .sub{color:var(--muted)}
  .head-rule{left:36px;top:62px;width:237px;height:3px;background:var(--rule)}
  .brand{left:352px;top:34px;display:flex;align-items:center;gap:6px;color:var(--red);font-size:26px;font-weight:700;letter-spacing:2px}
  .brand-dot{width:14px;height:14px;border-radius:50%;background:var(--ink)}
  .section-title{color:var(--red);font-size:14px;font-weight:700;line-height:15.5px}
  .tag{background:var(--panel);color:var(--muted);font-weight:700;font-size:11.5px;line-height:13.5px;padding:4px 6px}
  .copy{color:var(--body);font-size:9.3px;line-height:11.1px;text-align:justify}
  .figure-panel{background:var(--panel)}
  .caption{background:var(--panel);border-top:1px solid var(--red);padding:7px 6px 0}
  .caption .label{color:var(--red);font-size:10px;font-weight:700}
  .caption .desc{color:var(--muted);font-size:7.3px;font-weight:700;line-height:9px;margin-top:1px}
  .foot-rule{left:33px;width:420px;height:1px;background:var(--rule)}
  .folio{font-size:7.5px;color:var(--muted)}
  .data-sheet{left:232px;top:396px;width:240px;height:216px;background:#fff;box-shadow:0 1px 4px rgba(0,0,0,.25);padding:4px 5px;overflow:hidden}
  .data-sheet table{width:100%;border-collapse:collapse;font-size:4.6px;line-height:6.4px;color:#444}
  .data-sheet th{font-weight:400;text-align:left;border-bottom:1px solid var(--sheet-line);padding-bottom:1px}
  .data-sheet td{border-bottom:0.5px solid var(--sheet-line);white-space:nowrap}
  .data-sheet .num{text-align:right}
</style>
</head>
<body>

<section class="page page--left">
  <div class="abs running-head"><div class="kicker">USE YOUR DATA TO IMPROVE LOGISTICS</div><div class="sub">PROCESSES AND PROFITS</div></div>
  <div class="abs head-rule"></div>
  <div class="abs brand"><span class="brand-dot"></span>KVRD</div>

  <h2 class="abs section-title" style="left:34px;top:117px">A Better Way to Handle Multiple Quotes</h2>
  <div class="abs tag" style="left:34px;top:139px;width:188px">USE A TMS (TRANSPORTATION MANAGEMENT SYSTEM)</div>
  <p class="abs copy" style="left:34px;top:185px;width:188px">Is there a way to get multiple quotes without spending so much time and effort asking for quotes, reviewing them and then awarding the business? In a word, yes. If you use a Transportation Management System (TMS) you can enter the shipment information on your shipment once and get immediate quotes from multiple carriers (Fig. 2). You can select the carrier you want and get your shipment underway in about a minute. In addition to saving time and reducing stress, the TMS will permit you to print the BOL and Labels so your shipment is ready for the driver to pick up. You access the TMS via the web, so there is no special equipment to purchase. You will need accounts with each carrier and you should negotiate your own rates with them. The TMS will typically permit you to track shipments on all carriers, and it can also capture the quote information for reference later. Perhaps the most commonly overlooked, the data from all of your shipments is captured and retained in the TMS, so you can produce reports at the end of the month or on demand.</p>

  <div class="abs figure-panel" style="left:238px;top:138px;width:266px;height:272px">
    <svg width="266" height="272" viewBox="0 0 266 272" font-family="'Source Serif 4', Georgia, serif">
      <defs>
        <g id="chev-v" fill="none" stroke="#e3151f" stroke-width="2"><path d="M-4,-5 L0,-9 L4,-5"/><path d="M-4,5 L0,9 L4,5"/></g>
        <g id="chev-h" fill="none" stroke="#e3151f" stroke-width="2"><path d="M-5,-4 L-9,0 L-5,4"/><path d="M5,-4 L9,0 L5,4"/></g>
      </defs>
      <text x="162" y="15" font-size="9" font-weight="700" fill="#2a2a2a">Queries /Booking</text>
      <g font-size="14" font-weight="700" fill="#fff" text-anchor="middle">
        <circle cx="132" cy="35" r="12" fill="#b9b9b9"/><text x="132" y="40">T</text>
        <circle cx="174" cy="35" r="12" fill="#e3151f"/><text x="174" y="40">T</text>
        <circle cx="224" cy="35" r="12" fill="#b9b9b9"/><text x="224" y="40">T</text>
        <circle cx="234" cy="94" r="12" fill="#b9b9b9"/><text x="234" y="99">T</text>
        <circle cx="234" cy="141" r="12" fill="#b9b9b9"/><text x="234" y="146">T</text>
        <circle cx="234" cy="189" r="12" fill="#b9b9b9"/><text x="234" y="194">T</text>
        <circle cx="132" cy="246" r="12" fill="#b9b9b9"/><text x="132" y="251">T</text>
        <circle cx="174" cy="246" r="12" fill="#b9b9b9"/><text x="174" y="251">T</text>
        <circle cx="224" cy="246" r="12" fill="#b9b9b9"/><text x="224" y="251">T</text>
      </g>
      <use href="#chev-v" x="132" y="64"/><use href="#chev-v" x="174" y="64"/>
      <use href="#chev-v" x="132" y="217"/><use href="#chev-v" x="174" y="217"/>
      <g transform="translate(203,64) rotate(45)"><use href="#chev-v"/></g>
      <g transform="translate(203,217) rotate(-45)"><use href="#chev-v"/></g>
      <use href="#chev-h" x="205" y="94"/><use href="#chev-h" x="205" y="141"/><use href="#chev-h" x="205" y="189"/>
      <use href="#chev-h" x="104" y="139"/>
      <rect x="13" y="86" width="69" height="107" fill="#fff" stroke="#e3151f" stroke-width="1.5"/>
      <rect x="18" y="183" width="59" height="4" fill="#e3151f"/>
      <text x="47" y="144" font-size="12" font-weight="700" fill="#e3151f" text-anchor="middle">SHIPPER</text>
      <rect x="126" y="86" width="66" height="107" fill="#fff" stroke="#e3151f" stroke-width="1.5"/>
      <rect x="130" y="183" width="58" height="4" fill="#e3151f"/>
      <text x="132" y="144" font-size="12" font-weight="700" fill="#e3151f">TMS</text>
      <g font-size="7.5" font-weight="700" fill="#2a2a2a" text-anchor="middle">
        <text x="104" y="97">Quotes</text><text x="104" y="106">/Booking</text>
        <text x="104" y="188">Historical</text><text x="104" y="197">Data</text>
      </g>
    </svg>
  </div>
  <div class="abs caption" style="left:238px;top:414px;width:233px;height:50px">
    <div class="label">FIGURE 2.</div>
    <div class="desc">Using a TMS saves time by entering the quote request, receiving multiple quotes assigning the load and printing BOL and Shipping Labels in less than a minute</div>
  </div>

  <h2 class="abs section-title" style="left:34px;top:497px">Beyond the TMS</h2>
  <div class="abs tag" style="left:153px;top:493px;width:314px;height:20px;padding-top:3px">USING A 3PL</div>
  <p class="abs copy" style="left:34px;top:523px;width:434px">TMS systems are commonly web based and very easy to use. They usually require a monthly fee depending on the number of users and monthly shipments. There may also be a fee for setting up your carriers in the system to get started. What else can you do to improve your logistics system? If you utilize the services of a 3PL, you will often be able to get a TMS system for no charge as long as you book with their carriers. The 3PL is bringing much more business to the negotiating table than you will alone, so their rates are likely to be lower than yours. So, you get lower rates, spend less time quoting and booking as well as all the other benefits of a TMS while saving money. You also get a single invoice each month covering all of your shipments.</p>

  <div class="abs foot-rule" style="top:637px"></div>
  <div class="abs folio" style="left:459px;top:633px">03</div>
</section>

<section class="page page--right">
  <div class="abs running-head"><div class="kicker">USE YOUR DATA TO IMPROVE LOGISTICS</div><div class="sub">PROCESSES AND PROFITS</div></div>
  <div class="abs head-rule"></div>
  <div class="abs brand"><span class="brand-dot"></span>KVRD</div>

  <h2 class="abs section-title" style="left:34px;top:128px">3PL’s Help You Select the Best Mode at the Best Price</h2>
  <p class="abs copy" style="left:34px;top:150px;width:438px">With a 3PL, you also have access to a knowledgeable staff who can help you when your loads might be better served with a partial truckload quote. Some 3PL’s provide for putting your carriers in the TMS alongside their carriers and all the carriers bid against each other. If your carrier is selected, you will receive a bill from them and deal directly with them for any service issues. If you use the 3PL’s carriers, you get a combined invoice from the 3PL.</p>

  <h2 class="abs section-title" style="left:34px;top:245px">Data Stuck In the Cloud Is No Earthly Good</h2>
  <p class="abs copy" style="left:34px;top:267px;width:438px">Your logistics system is constantly generating data including pricing by lane, cost per pound, “geographic center of gravity,” and much more. To ignore this information is to lose a great opportunity to understand your system at a deeper level and make informed decisions to improve your performance. Whether it is a big deal like establishing a new distribution center that will result in shorter delivery times at less cost or relatively simple things like combining loads to take advantage of weight breaks, you will benefit greatly from mining the information your system contains.</p>

  <h2 class="abs section-title" style="left:34px;top:367px">Data Must be Processed<br>and Evaluated Properly<br>to Be Useful</h2>
  <p class="abs copy" style="left:34px;top:418px;width:176px">KVRD can help organize, analyze and utilize your data. KVRD arranges for our clients to work with major 3PL’s providing access not only to their robust TMS systems, but also their volume based pricing. You get all the benefits of a TMS, plus better rates. You also get custom analysis of your data prepared by KVRD from the information captured and stored in the TMS. When your information is exported from the TMS, it comes out in a spreadsheet with no formatting, filtering or meaningful summaries (Fig 3).</p>

  <div class="abs data-sheet">
    <table>
      <thead><tr><th>Client</th><th>Invoice</th><th>Date</th><th>Carrier</th><th>Zip</th><th>State</th><th class="num">Charge</th></tr></thead>
      <tbody>
        <tr><td>Ace Parts</td><td>1247824</td><td>8/2/16</td><td>AAA</td><td>85043</td><td>CAN</td><td class="num">875.00</td></tr>
        <tr><td>Ace Parts</td><td>1247831</td><td>8/3/16</td><td>BBB</td><td>85043</td><td>CAN</td><td class="num">730.00</td></tr>
        <tr><td>Ace Parts</td><td>1247902</td><td>8/3/16</td><td>CCC</td><td>60023</td><td>CAN</td><td class="num">357.00</td></tr>
        <tr><td>Ace Parts</td><td>1247955</td><td>8/4/16</td><td>DDD</td><td>76336</td><td>CAN</td><td class="num">250.00</td></tr>
        <tr><td>Ace Parts</td><td>1248011</td><td>8/4/16</td><td>EEE</td><td>45459</td><td>CAN</td><td class="num">284.00</td></tr>
        <tr><td>Ace Parts</td><td>1248063</td><td>8/5/16</td><td>FFF</td><td>13126</td><td>DEL</td><td class="num">173.04</td></tr>
        <tr><td>Ace Parts</td><td>1248120</td><td>8/5/16</td><td>AAA</td><td>55075</td><td>DEL</td><td class="num">191.57</td></tr>
        <tr><td>Ace Parts</td><td>1248177</td><td>8/8/16</td><td>BBB</td><td>17536</td><td>DEL</td><td class="num">129.94</td></tr>
        <tr><td>Ace Parts</td><td>1248230</td><td>8/8/16</td><td>CCC</td><td>67322</td><td>DEL</td><td class="num">125.11</td></tr>
        <tr><td>Ace Parts</td><td>1248288</td><td>8/9/16</td><td>DDD</td><td>77240</td><td>DEL</td><td class="num">408.44</td></tr>
        <tr><td>Ace Parts</td><td>1248341</td><td>8/9/16</td><td>EEE</td><td>40021</td><td>DEL</td><td class="num">141.83</td></tr>
        <tr><td>Ace Parts</td><td>1248396</td><td>8/10/16</td><td>FFF</td><td>50112</td><td>DEL</td><td class="num">165.74</td></tr>
        <tr><td>Ace Parts</td><td>1248452</td><td>8/10/16</td><td>AAA</td><td>17421</td><td>DEL</td><td class="num">548.07</td></tr>
        <tr><td>Ace Parts</td><td>1248507</td><td>8/11/16</td><td>BBB</td><td>53821</td><td>DEL</td><td class="num">142.46</td></tr>
        <tr><td>Ace Parts</td><td>1248563</td><td>8/11/16</td><td>CCC</td><td>76336</td><td>DEL</td><td class="num">325.84</td></tr>
        <tr><td>Ace Parts</td><td>1248618</td><td>8/12/16</td><td>DDD</td><td>71115</td><td>DEL</td><td class="num">247.20</td></tr>
        <tr><td>Ace Parts</td><td>1248674</td><td>8/12/16</td><td>EEE</td><td>43311</td><td>DEL</td><td class="num">143.79</td></tr>
        <tr><td>Ace Parts</td><td>1248729</td><td>8/15/16</td><td>FFF</td><td>65203</td><td>DEL</td><td class="num">131.37</td></tr>
        <tr><td>Ace Parts</td><td>1248785</td><td>8/15/16</td><td>AAA</td><td>60502</td><td>DEL</td><td class="num">125.67</td></tr>
        <tr><td>Ace Parts</td><td>1248840</td><td>8/16/16</td><td>BBB</td><td>91761</td><td>DEL</td><td class="num">158.77</td></tr>
        <tr><td>Ace Parts</td><td>1248896</td><td>8/16/16</td><td>CCC</td><td>89502</td><td>DEL</td><td class="num">131.37</td></tr>
        <tr><td>Ace Parts</td><td>1248951</td><td>8/17/16</td><td>DDD</td><td>62286</td><td>DEL</td><td class="num">125.67</td></tr>
        <tr><td>Ace Parts</td><td>1249007</td><td>8/17/16</td><td>EEE</td><td>84653</td><td>DEL</td><td class="num">174.01</td></tr>
        <tr><td>Ace Parts</td><td>1249062</td><td>8/18/16</td><td>FFF</td><td>43311</td><td>DEL</td><td class="num">142.46</td></tr>
        <tr><td>Ace Parts</td><td>1249118</td><td>8/18/16</td><td>AAA</td><td>76335</td><td>DEL</td><td class="num">340.47</td></tr>
        <tr><td>Ace Parts</td><td>1249173</td><td>8/19/16</td><td>BBB</td><td>55075</td><td>DEL</td><td class="num">142.46</td></tr>
        <tr><td>Ace Parts</td><td>1249229</td><td>8/19/16</td><td>CCC</td><td>95961</td><td>DEL</td><td class="num">155.06</td></tr>
        <tr><td>Ace Parts</td><td>1249284</td><td>8/22/16</td><td>DDD</td><td>53821</td><td>DEL</td><td class="num">564.73</td></tr>
        <tr><td>Ace Parts</td><td>1249340</td><td>8/22/16</td><td>EEE</td><td>69160</td><td>DEL</td><td class="num">128.84</td></tr>
        <tr><td>Ace Parts</td><td>1249395</td><td>8/23/16</td><td>FFF</td><td>17421</td><td>DEL</td><td class="num">154.07</td></tr>
      </tbody>
    </table>
  </div>
  <div class="abs caption" style="left:34px;top:582px;width:198px;height:32px;padding-top:6px">
    <div class="label">FIGURE 3.</div>
    <div class="desc" style="font-size:7.8px">Lots of data, not much help</div>
  </div>

  <div class="abs foot-rule" style="top:636px"></div>
  <div class="abs folio" style="left:466px;top:640px">04</div>
</section>

</body>
</html>
```